Expedition Cruise Sales Website for the Polar Regions (Antarctica & Arctic)

This will be a website for selling cruises.
This site should have a homepage, a ship page, destinations, and itineraries.
I have created a file specifying each page, and it is attached.
Pages:
1. Home
2. Cruise Lines
- 2.1 Ships
3. Destinations
- 3.1 Region - 3.2 Country - 3.3 City
4. Itineraries
- 4.1 Itinerary
5. Blog / Travel Tips 6. About Us
7. Contact
Please take a look on the attached pdf
Target Market(s)
Expedition Travelers
Coding
Coded - Design and coding required
Number of Pages Required
5+ page
Font styles to use
Look and feel
Each slider illustrates characteristics of the customer's brand and the style your logo design should communicate.

```html
<!DOCTYPE html>
<html lang="en">
<head>
<meta charset="utf-8">
<title>Travel Tips – Polaris Voyages</title>
<link href="https://fonts.googleapis.com/css2?family=Plus+Jakarta+Sans:wght@400;500;600;700&display=swap" rel="stylesheet">
<style>
:root{
  --blue:#3b78c3;
  --blue-band:#3a74b8;
  --blue-text:#2f6fc0;
  --pale:#cfdff0;
  --navy:#1c2a48;
  --navy-btn:#10244a;
  --ink:#141a26;
  --grey:#8a909a;
  --line:#e2e5ea;
  --white:#ffffff;
  --chat:#3cc356;
}
*{box-sizing:border-box;margin:0;padding:0}
html,body{width:1200px;height:3070px;overflow:hidden}
body{position:relative;font-family:'Plus Jakarta Sans',sans-serif;color:var(--ink);background:var(--white)}
.abs{position:absolute}

/* hero */
.hero{left:0;top:0;width:1200px;height:312px;background:linear-gradient(100deg,#3d5a3a 0%,#5b7a55 25%,#9aa79a 45%,#6f8fa6 65%,#3c6c8e 85%,#2e5d80 100%)}
.hero::after{content:"";position:absolute;inset:0;background:linear-gradient(180deg,rgba(20,35,60,.55) 0%,rgba(20,35,60,.15) 40%,rgba(20,35,60,.2) 100%)}
.nav{left:0;top:0;width:1200px;height:100px;z-index:2}
.brand{left:66px;top:30px;display:flex;align-items:center;gap:10px;color:var(--white);font-weight:600;font-size:27px}
.brand .mark{width:34px;height:34px;border-radius:50%;background:var(--white)}
.menu-item{top:44px;font-size:9.5px;color:var(--white);font-weight:500;white-space:nowrap}
.menu-item.active{color:#7fb1ec}
.phone{left:906px;top:41px;display:flex;align-items:center;gap:6px;color:var(--white);font-size:12.5px;font-weight:600}
.book{left:1025px;top:33px;width:100px;height:31px;background:var(--blue);color:var(--white);font-size:10px;font-weight:600;display:flex;align-items:center;justify-content:center}
.hero-title{left:0;top:132px;width:1200px;text-align:center;color:var(--white);font-size:42px;font-weight:700;z-index:2}
.crumb{left:0;top:191px;width:1200px;text-align:center;color:var(--white);font-size:12px;font-weight:500;z-index:2;word-spacing:10px}

/* section heads */
.sec-title{left:0;width:1200px;text-align:center;font-size:22.5px;font-weight:700}
.sec-sub{left:0;width:1200px;text-align:center;font-size:9px;color:#333}

/* cards */
.card{width:250px;background:var(--white);border:1px solid var(--line)}
.card .photo{height:156px;position:relative}
.tag{position:absolute;left:8px;top:7px;background:var(--white);font-size:8.5px;font-weight:500;padding:4px 5px}
.card .body{padding:0 18px}
.date{margin-top:18px;font-size:9px;color:var(--blue-text);font-weight:600}
.card h3{margin-top:13px;font-size:13px;line-height:15px;font-weight:600;width:192px}
.card p{margin-top:13px;font-size:8.6px;line-height:12.3px;color:var(--grey);width:206px}
.go{width:31px;height:31px;border-radius:50%;background:var(--pale);display:flex;align-items:center;justify-content:center;margin-top:20px}
.art{height:356px}
.guide{height:326px}
.guide h3{margin-top:18px;width:200px}

/* pagination */
.pager{left:0;top:1211px;width:1200px;display:flex;justify-content:center;align-items:center;gap:6px;font-size:9px}
.pager span{width:25px;height:25px;border:1px solid var(--line);border-radius:50%;display:flex;align-items:center;justify-content:center}
.pager .cur{background:var(--pale);border-color:var(--pale)}
.pager .arr{border:none;width:30px}

.guides{left:262px;top:1286px;width:676px;height:518px;background:var(--pale)}
.dots{left:0;top:1746px;width:1200px;display:flex;justify-content:center;gap:6px}
.dots i{width:9px;height:9px;border-radius:50%;background:#a8b3c0}
.dots i.on{background:var(--blue)}

/* itineraries */
.itin{width:250px;height:256px;background:var(--white);border:1px solid var(--line)}
.itin .photo{height:156px}
.itin h3{margin:22px 18px 0;font-size:12.5px;font-weight:600}
.itin p{margin:8px 18px 0;font-size:8.8px;line-height:12.5px;color:#333;width:194px}
.slide-btn{width:24px;height:24px;border-radius:50%;background:var(--white);box-shadow:0 1px 4px rgba(0,0,0,.2);display:flex;align-items:center;justify-content:center;font-size:10px;color:#666}

/* newsletter */
.news{left:0;top:2295px;width:1200px;height:426px;background:var(--blue-band)}
.news-photo{left:707px;top:2239px;width:387px;height:482px;background:linear-gradient(180deg,#dfe3e8 0%,#cfd6de 45%,#8d9aa8 62%,#5f6f82 72%,#c9d6e2 85%,#eef3f7 100%)}
.news h2{position:absolute;left:106px;top:95px;font-size:31px;line-height:35px;font-weight:400;color:var(--white)}
.news h2 b{font-weight:700}
.news .lead{position:absolute;left:106px;top:177px;font-size:11.5px;line-height:14px;color:var(--white);width:400px}
.field{position:absolute;width:234px;height:30px;background:var(--white);font-size:9px;color:#222;padding-left:13px;display:flex;align-items:center}
.submit{position:absolute;left:106px;top:315px;width:100px;height:30px;background:var(--navy-btn);color:var(--white);font-size:9.5px;font-weight:600;display:flex;align-items:center;justify-content:center}

/* footer */
.footer{left:0;top:2721px;width:1200px;height:349px;background:linear-gradient(180deg,#1e2d4d 0%,#24365a 55%,#2a3f66 100%);color:var(--white)}
.f-brand{position:absolute;left:106px;top:78px;display:flex;align-items:center;gap:10px;font-size:27px;font-weight:600}
.f-brand .mark{width:40px;height:40px;border-radius:50%;background:var(--white)}
.f-about{position:absolute;left:106px;top:137px;width:372px;font-size:9.5px;line-height:19px}
.f-h{position:absolute;font-size:13px;font-weight:600}
.f-line{position:absolute;display:flex;align-items:center;gap:8px;font-size:11px}
.socials{position:absolute;left:587px;top:192px;display:flex;gap:8px}
.socials i{width:30px;height:30px;border:1px solid rgba(255,255,255,.8);border-radius:50%}
.links{position:absolute;font-size:9.3px;line-height:19px}
.rule{position:absolute;left:106px;top:280px;width:988px;height:1px;background:rgba(255,255,255,.2)}
.copy{position:absolute;left:106px;top:311px;font-size:9.5px}
.top-arrow{position:absolute;left:1128px;top:284px}
.help{left:1056px;top:2694px;width:112px;height:50px;background:var(--white);border-radius:3px;box-shadow:0 1px 5px rgba(0,0,0,.2);z-index:3}
.help .dot{position:absolute;left:67px;top:-20px;width:36px;height:36px;border-radius:50%;background:var(--chat);border:3px solid var(--white)}
.help .t1{position:absolute;left:9px;top:12px;font-size:8px}
.help .t2{position:absolute;left:9px;top:23px;font-size:13px;color:var(--blue);font-weight:700;white-space:nowrap}
.help .t2 small{font-size:6.5px;color:#222;font-weight:500}
.help .t3{position:absolute;left:9px;top:37px;font-size:6.5px}
</style>
</head>
<body>

<div class="abs hero" role="img" aria-label="Tropical cliffside beach with turquoise sea and swimmers"></div>
<header class="abs nav">
  <div class="abs brand"><span class="mark"></span>Polaris Voyages</div>
  <nav>
    <span class="abs menu-item active" style="left:378px">Home</span>
    <span class="abs menu-item" style="left:442px">Cruise lines</span>
    <span class="abs menu-item" style="left:530px">Destinations</span>
    <span class="abs menu-item" style="left:621px">Itineraries</span>
    <span class="abs menu-item" style="left:703px">Blog</span>
    <span class="abs menu-item" style="left:763px">About us</span>
    <span class="abs menu-item" style="left:839px">Contact</span>
  </nav>
  <div class="abs phone"><svg width="11" height="11" viewBox="0 0 24 24" fill="none" stroke="#fff" stroke-width="2"><path d="M5 3h4l2 5-2.5 1.5a11 11 0 0 0 6 6L16 13l5 2v4a2 2 0 0 1-2 2A16 16 0 0 1 3 5a2 2 0 0 1 2-2z"/></svg>555.018.2740</div>
  <div class="abs book">Book Now!</div>
</header>
<h1 class="abs hero-title">Travel Tips</h1>
<div class="abs crumb">Home &gt;&gt; Blog</div>

<h2 class="abs sec-title" style="top:362px">Recent Articles</h2>
<div class="abs sec-sub" style="top:399px">Contrary to popular belief, lorem ipsum is not simply random text.</div>

<article class="abs card art" style="left:200px;top:442px"><div class="photo" role="img" aria-label="Expedition ship beside icebergs and snowy mountains" style="background:linear-gradient(180deg,#9db8d6,#e6edf4 50%,#3d66a3)"><span class="tag">Cruise news</span></div><div class="body"><div class="date">June 16, 2025</div><h3>Lorem ipsum is simply dummy text of the printing and typesetting</h3><p>It is a long established fact that a reader will be distracted by the readable content of a page when looking at its layout.</p><div class="go"><svg width="9" height="7" viewBox="0 0 9 7"><path d="M0 3.5h8M5.5 1l2.5 2.5L5.5 6" stroke="#1c2a48" fill="none"/></svg></div></div></article>
<article class="abs card art" style="left:475px;top:442px"><div class="photo" role="img" aria-label="Aerial view of tropical island with resort beach" style="background:linear-gradient(180deg,#4f8fd0,#2a9bb8 45%,#5aa468 70%,#d8cfb0)"><span class="tag">Travel tips</span></div><div class="body"><div class="date">June 16, 2025</div><h3>Lorem ipsum is simply dummy text of the printing and typesetting</h3><p>It is a long established fact that a reader will be distracted by the readable content of a page when looking at its layout.</p><div class="go"><svg width="9" height="7" viewBox="0 0 9 7"><path d="M0 3.5h8M5.5 1l2.5 2.5L5.5 6" stroke="#1c2a48" fill="none"/></svg></div></div></article>
<article class="abs card art" style="left:750px;top:442px"><div class="photo" role="img" aria-label="Navy expedition ship on icy water" style="background:linear-gradient(180deg,#8fb3de,#dbe6f2 45%,#283d6e 60%,#4a6c9f)"><span class="tag">Cruise news</span></div><div class="body"><div class="date">June 16, 2025</div><h3>Lorem ipsum is simply dummy text of the printing and typesetting</h3><p>It is a long established fact that a reader will be distracted by the readable content of a page when looking at its layout.</p><div class="go"><svg width="9" height="7" viewBox="0 0 9 7"><path d="M0 3.5h8M5.5 1l2.5 2.5L5.5 6" stroke="#1c2a48" fill="none"/></svg></div></div></article>

<article class="abs card art" style="left:200px;top:823px"><div class="photo" role="img" aria-label="Expedition ship beside icebergs and snowy mountains" style="background:linear-gradient(180deg,#9db8d6,#e6edf4 50%,#3d66a3)"><span class="tag">Cruise news</span></div><div class="body"><div class="date">June 16, 2025</div><h3>Lorem ipsum is simply dummy text of the printing and typesetting</h3><p>It is a long established fact that a reader will be distracted by the readable content of a page when looking at its layout.</p><div class="go"><svg width="9" height="7" viewBox="0 0 9 7"><path d="M0 3.5h8M5.5 1l2.5 2.5L5.5 6" stroke="#1c2a48" fill="none"/></svg></div></div></article>
<article class="abs card art" style="left:475px;top:823px"><div class="photo" role="img" aria-label="Snorkeler swimming in clear turquoise water" style="background:linear-gradient(160deg,#7fd3d0,#2fb4b8 50%,#168a9a)"><span class="tag">Travel tips</span></div><div class="body"><div class="date">June 16, 2025</div><h3>Lorem ipsum is simply dummy text of the printing and typesetting</h3><p>It is a long established fact that a reader will be distracted by the readable content of a page when looking at its layout.</p><div class="go"><svg width="9" height="7" viewBox="0 0 9 7"><path d="M0 3.5h8M5.5 1l2.5 2.5L5.5 6" stroke="#1c2a48" fill="none"/></svg></div></div></article>
<article class="abs card art" style="left:750px;top:823px"><div class="photo" role="img" aria-label="Cruise ship arriving at a historic harbour city at dusk" style="background:linear-gradient(180deg,#5a6f95,#c69a6a 40%,#2d4a78 65%,#1f3a66)"><span class="tag">Cruise news</span></div><div class="body"><div class="date">June 16, 2025</div><h3>Lorem ipsum is simply dummy text of the printing and typesetting</h3><p>It is a long established fact that a reader will be distracted by the readable content of a page when looking at its layout.</p><div class="go"><svg width="9" height="7" viewBox="0 0 9 7"><path d="M0 3.5h8M5.5 1l2.5 2.5L5.5 6" stroke="#1c2a48" fill="none"/></svg></div></div></article>

<div class="abs pager"><span class="arr">‹</span><span>1</span><span class="cur">2</span><span>3</span><span>4</span><span>5</span><span>···</span><span>15</span><span class="arr">›</span></div>

<div class="abs guides"></div>
<h2 class="abs sec-title" style="top:1335px;font-size:20px">Destination Guides</h2>
<article class="abs card guide" style="left:200px;top:1390px"><div class="photo" role="img" aria-label="Couple enjoying a cave pool" style="background:linear-gradient(180deg,#3d3a30,#5e7a60 50%,#2e8a8a)"></div><div class="body"><h3>Lorem ipsum is simply dummy text of the printing</h3><p>It is a long established fact that a reader will be distracted by the readable content of a page when looking at its layout.</p><div class="go" style="margin-top:28px"><svg width="9" height="7" viewBox="0 0 9 7"><path d="M0 3.5h8M5.5 1l2.5 2.5L5.5 6" stroke="#1c2a48" fill="none"/></svg></div></div></article>
<article class="abs card guide" style="left:475px;top:1390px"><div class="photo" role="img" aria-label="Go-kart racing on a mountain lake track" style="background:linear-gradient(180deg,#6d8a9c,#8a9a8e 40%,#b33a3a 70%,#3c3c3c)"></div><div class="body"><h3>Lorem ipsum is simply dummy text of the printing</h3><p>It is a long established fact that a reader will be distracted by the readable content of a page when looking at its layout.</p><div class="go" style="margin-top:28px"><svg width="9" height="7" viewBox="0 0 9 7"><path d="M0 3.5h8M5.5 1l2.5 2.5L5.5 6" stroke="#1c2a48" fill="none"/></svg></div></div></article>
<article class="abs card guide" style="left:750px;top:1390px"><div class="photo" role="img" aria-label="Whale tail above the sea at sunset with birds" style="background:linear-gradient(180deg,#e39a4f,#f2c281 40%,#7c8fa6 65%,#4a6383)"></div><div class="body"><h3>Lorem ipsum is simply dummy text of the printing</h3><p>It is a long established fact that a reader will be distracted by the readable content of a page when looking at its layout.</p><div class="go" style="margin-top:28px"><svg width="9" height="7" viewBox="0 0 9 7"><path d="M0 3.5h8M5.5 1l2.5 2.5L5.5 6" stroke="#1c2a48" fill="none"/></svg></div></div></article>
<div class="abs dots"><i></i><i class="on"></i><i></i><i></i></div>

<h2 class="abs sec-title" style="top:1853px;font-size:20px">Travel Itineraries</h2>
<article class="abs itin" style="left:63px;top:1908px"><div class="photo" role="img" aria-label="Waterfall plunging into a turquoise river" style="background:linear-gradient(180deg,#d7e6ef,#7fc3d2 50%,#2a9bb0)"></div><h3>Chichen itza mayan ruins</h3><p>There are many variations of passages of lorem ipsum available, but the majority have suffered alteration in some form.</p></article>
<article class="abs itin" style="left:337px;top:1908px"><div class="photo" role="img" aria-label="Lakeside lodge below snowy mountains and pine forest" style="background:linear-gradient(180deg,#4d7ab8,#dfe7ee 30%,#2f5a3c 55%,#2a9a9a)"></div><h3>Jeep adventure to todos santos</h3><p>There are many variations of passages of lorem ipsum available, but the majority have suffered alteration in some form.</p></article>
<article class="abs itin" style="left:612px;top:1908px"><div class="photo" role="img" aria-label="Historic château above an old city in autumn" style="background:linear-gradient(180deg,#dfe4ea,#9a6b55 40%,#5e6d4e 70%,#b08a5a)"></div><h3>Cozumel dive &amp; drive</h3><p>There are many variations of passages of lorem ipsum available, but the majority have suffered alteration in some form.</p></article>
<article class="abs itin" style="left:888px;top:1908px"><div class="photo" role="img" aria-label="Alpine lake among rocky peaks and forest" style="background:linear-gradient(180deg,#cfd8e0,#6f7c78 35%,#2f4d33 60%,#38a6a8)"></div><h3>Canopy tour</h3><p>There are many variations of passages of lorem ipsum available, but the majority have suffered alteration in some form.</p></article>
<div class="abs slide-btn" style="left:50px;top:2024px">‹</div>
<div class="abs slide-btn" style="left:1125px;top:2024px">›</div>

<section class="abs news">
  <h2>Get cruise deals <b>directly<br>in your inbox</b></h2>
  <p class="lead">Subscribe now and set sail on a journey of endless adventure with our exclusive cruise newsletter</p>
  <div class="field" style="left:106px;top:227px">First Name</div>
  <div class="field" style="left:353px;top:227px">Last Name</div>
  <div class="field" style="left:106px;top:271px">Email Address...</div>
  <div class="field" style="left:353px;top:271px">Mobile Number</div>
  <div class="submit">Submit</div>
</section>
<div class="abs news-photo" role="img" aria-label="Expedition cruise ship moored among ice floes under a snowy cliff"></div>

<footer class="abs footer">
  <div class="f-brand"><span class="mark"></span>Polaris Voyages</div>
  <p class="f-about">Lorem Ipsum is simply dummy text of the printing and typesetting industry. Lorem Ipsum has been the industry's standard dummy text ever since the 1500s, when an unknown printer took a galley of type and scrambled it to make a type specimen book.</p>
  <div class="f-h" style="left:587px;top:73px">Contct Us</div>
  <div class="f-line" style="left:587px;top:104px"><svg width="11" height="11" viewBox="0 0 24 24" fill="none" stroke="#fff" stroke-width="2"><path d="M5 3h4l2 5-2.5 1.5a11 11 0 0 0 6 6L16 13l5 2v4a2 2 0 0 1-2 2A16 16 0 0 1 3 5a2 2 0 0 1 2-2z"/></svg>555.018.2740</div>
  <div class="f-line" style="left:587px;top:131px;font-size:9.5px"><svg width="10" height="9" viewBox="0 0 10 9"><path d="M0 3l5-3 5 3v6H0z" fill="#fff"/></svg>support@polarisvoyages.com</div>
  <div class="f-h" style="left:587px;top:165px">Follow us</div>
  <div class="socials"><i></i><i></i><i></i><i></i></div>
  <div class="f-h" style="left:819px;top:73px">Quick Links</div>
  <div class="links" style="left:819px;top:102px">Home<br>Cruise Lines<br>Destinations<br>Itineraries<br>Blog<br>About Us<br>Contact</div>
  <div class="links" style="left:924px;top:102px">FAQ<br>Privacy Policy<br>Terms and Conditions<br>Booking Confirmation</div>
  <div class="rule"></div>
  <div class="copy">© 2025 <b>Polaris Voyages</b> All Rights Reserved</div>
  <svg class="top-arrow" width="18" height="20" viewBox="0 0 18 20"><path d="M9 0L18 20 9 14 0 20z" fill="#fff"/></svg>
</footer>

<div class="abs help"><span class="dot"></span><span class="t1">Available</span><span class="t2">24/7 <small>to Assist with</small></span><span class="t3">Any Questions</span></div>

</body>
</html>
```